BrivoTerna. Lantern of the Steady Harvest. Business card

Professional business card for BrivoTerna (Lantern of the Steady Harvest)
My rationale: Strategy-> Execution-> Results-> Value that lead to the BrivoTerna name: We put the Lantern of the Steady Harvest.
We deliver value to our customers helping them at defining a good strategy (cyan arrow). 90% of well formulated strategies fail due to poor execution so we also consider strategical execution very important (green arrow). Due to the execution we obtain the results (blue arrow). Finally, the results provide feedback to redefine strategy, and the new strategy has to be executed and new results obtained providing new feedback and on and on. It's like a wheel that finally, must create corporate value: value for shareholders, staholders, employees, providers...-

Target Market(s)

CEOs and steering comitees , invewrnent funds

Industry/Entity Type

Business Consultant

Contact Information for Business Card

Teodoro Vinsquel
CEO & Founder
teodoro.vinsquel@brivoterna-example.com
Mobile: +34 655.803.912
www.brivoterna-example.com

Colors

Designer to choose colors to be used in the design.

Requirements
Nice to have
• Nice to hace the words: Strategy, execution, results
• Nice to vave the claim: Lantern of the Steady Harvest
• The three colors should be shown:
• cyan for STRATEGY
• green for EXECUTION
• blue for RESULTS
Should not have
• Complete black background

```html
<!DOCTYPE html>
<html lang="en">
<head>
<meta charset="utf-8">
<title>BrivoTerna – Business Card</title>
<link rel="stylesheet" href="https://fonts.googleapis.com/css2?family=Open+Sans:wght@400;600;700&display=swap">
<style>
  :root {
    --backdrop: #e6e8ec;
    --card-white: #ffffff;
    --brand-navy: #0b2f91;
    --brand-cyan: #00aeef;
    --brand-green: #8dc63f;
    --text-light: #ffffff;
    --card-shadow: 0 18px 40px rgba(20, 30, 60, 0.18);
  }
  * { box-sizing: border-box; margin: 0; padding: 0; }
  html, body {
    width: 1200px; height: 960px; overflow: hidden;
    background: var(--backdrop);
    font-family: "Open Sans", Arial, sans-serif;
  }
  .canvas { position: relative; width: 1200px; height: 960px; }

  .card {
    position: absolute; width: 620px; height: 360px;
    border-radius: 4px; overflow: hidden;
    box-shadow: var(--card-shadow);
  }

  /* Back side */
  .card-back { left: 460px; top: 80px; background: var(--brand-cyan); }
  .card-back .brand-block {
    position: absolute; left: 0; right: 0; top: 120px;
    display: flex; align-items: center; justify-content: center; gap: 16px;
  }
  .card-back .brand-dot {
    width: 26px; height: 26px; border-radius: 50%; background: var(--brand-navy);
  }
  .card-back .brand-name {
    font-weight: 700; font-size: 58px; color: var(--brand-navy); letter-spacing: -1px;
  }
  .card-back .back-url {
    position: absolute; left: 0; right: 0; bottom: 56px; text-align: center;
    font-size: 15px; letter-spacing: 2px; color: var(--brand-navy);
  }

  /* Front side */
  .card-front { left: 120px; top: 520px; background: var(--card-white); }
  .card-front .front-shape { position: absolute; inset: 0; }
  .card-front .brand-block {
    position: absolute; left: 36px; top: 120px;
    display: flex; align-items: center; gap: 12px;
  }
  .card-front .brand-dot {
    width: 18px; height: 18px; border-radius: 50%; background: var(--brand-green);
  }
  .card-front .brand-name {
    font-weight: 700; font-size: 40px; color: var(--brand-navy); letter-spacing: -1px;
  }
  .contact {
    position: absolute; right: 30px; top: 66px; text-align: right;
    color: var(--text-light);
  }
  .contact .person-name {
    font-weight: 700; font-size: 22px; color: var(--brand-green); letter-spacing: 0.5px;
  }
  .contact .person-role { font-size: 14px; margin-top: 2px; margin-bottom: 22px; }
  .contact .line {
    display: flex; justify-content: flex-end; align-items: center; gap: 8px;
    font-size: 14px; line-height: 1; margin-bottom: 11px;
  }
  .contact .icon { width: 14px; height: 14px; flex: none; }
</style>
</head>
<body>
<main class="canvas">

  <section class="card card-back" aria-label="Business card, back side">
    <div class="brand-block">
      <span class="brand-dot"></span>
      <span class="brand-name">BrivoTerna</span>
    </div>
    <p class="back-url">www.brivoterna-example.com</p>
  </section>

  <section class="card card-front" aria-label="Business card, front side">
    <svg class="front-shape" viewBox="0 0 620 360" width="620" height="360" aria-hidden="true">
      <path d="M396 0 Q236 80 212 360 L620 360 L620 0 Z" fill="var(--brand-cyan)"/>
      <path d="M414 0 Q252 84 232 360 L620 360 L620 0 Z" fill="var(--card-white)"/>
      <path d="M428 0 Q266 88 246 360 L620 360 L620 0 Z" fill="var(--brand-navy)"/>
    </svg>

    <div class="brand-block">
      <span class="brand-name">BrivoTerna</span>
      <span class="brand-dot"></span>
    </div>

    <div class="contact">
      <p class="person-name">Teodoro Vinsquel</p>
      <p class="person-role">CEO &amp; Founder</p>
      <p class="line">+34 655.803.912
        <svg class="icon" viewBox="0 0 14 14"><rect x="3.5" y="1" width="7" height="12" rx="1.2" fill="none" stroke="var(--brand-green)" stroke-width="1.4"/></svg>
      </p>
      <p class="line">teodoro.vinsquel@brivoterna-example.com
        <svg class="icon" viewBox="0 0 14 14"><rect x="1" y="3" width="12" height="8" fill="var(--brand-green)"/><path d="M1 3 L7 8 L13 3" fill="none" stroke="var(--brand-navy)" stroke-width="1.1"/></svg>
      </p>
      <p class="line">www.brivoterna-example.com
        <svg class="icon" viewBox="0 0 14 14"><circle cx="7" cy="7" r="5.8" fill="none" stroke="var(--brand-green)" stroke-width="1.2"/><ellipse cx="7" cy="7" rx="2.5" ry="5.8" fill="none" stroke="var(--brand-green)" stroke-width="1"/><path d="M1.2 7 H12.8" stroke="var(--brand-green)" stroke-width="1"/></svg>
      </p>
    </div>
  </section>

</main>
</body>
</html>
```